Varentoria Business Card and Letter Head

We are a leadership assessment consultancy based in Sydney, Australia. We help executive-level decison-makers select leaders for more senior level roles in corporate and government organisations. Our methodology is based on the latest research from the field of neuroscience.
We need a business card design and matching letter head that presents our company, Varentoria, as a:
1. trusted adviser to senior executive-level decison makers
2. niche consultancy who are experts in the field of assessing leadership talent
3. results-focused solution provider who balance scientific methods with pragmatic solutions
The following company details should be used in all designs:
Company Name: Varentoria
Details (for business card):
Derek Hanford
Prime Capacity Officer
Level 29, Marlow Tower
7 Marlow Square
Sydney, NSW 2000 Australia
Phone: 1300 582 714
Mobile: 0412 637 258
Email: derek.hanford@varentoria-example.com.au
Website: varentoria-example.com.au
I have attached the logo for Varentoria (for both a white and black background) - your business card and letter head designs must incoporate this logo and colour scheme.
Thanks for your interest in this project, I'm looking forward to receiving your ideas.
Regards,
Derek
Target Market(s)
Executive-level decison-makers in corporate and government organisations (e.g., CEO, VP, Head of Human Resources)
Industry/Entity Type
Leadership
Look and feel

```html
<!DOCTYPE html>
<html lang="en">
<head>
<meta charset="utf-8">
<title>Varentoria Business Card</title>
<link href="https://fonts.googleapis.com/css2?family=Open+Sans:wght@400;600;700&display=swap" rel="stylesheet">
<style>
  :root {
    --backdrop: #ecebe8;
    --card: #ffffff;
    --charcoal: #444446;
    --ink: #333333;
    --muted: #5a5a5a;
    --red: #b5281f;
    --rule: #cfcfcf;
    --on-dark: #ffffff;
  }
  * { margin: 0; padding: 0; box-sizing: border-box; }
  html, body {
    width: 1200px; height: 469px; overflow: hidden;
    background: var(--backdrop);
    font-family: "Open Sans", Arial, sans-serif;
  }
  .stage { position: relative; width: 1200px; height: 469px; }
  .card {
    position: absolute; top: 83px; width: 525px; height: 299px;
    background: var(--card); overflow: hidden;
    box-shadow: 0 2px 6px rgba(0,0,0,0.18);
  }
  .card--front { left: 55px; }
  .card--back { left: 610px; }
  .card__wave { position: absolute; left: 0; top: 0; width: 525px; height: 299px; }
  .brand { position: absolute; display: flex; align-items: center; }
  .brand__mark { background: var(--charcoal); }
  .brand__name { color: var(--charcoal); font-weight: 600; letter-spacing: -0.5px; line-height: 1; white-space: nowrap; }
  .card--front .brand { left: 40px; top: 126px; gap: 9px; }
  .card--front .brand__mark { width: 40px; height: 40px; }
  .card--front .brand__name { font-size: 27px; }
  .card--back .brand { left: 130px; top: 98px; gap: 12px; }
  .card--back .brand__mark { width: 48px; height: 48px; }
  .card--back .brand__name { font-size: 34px; }
  .divider { position: absolute; left: 268px; top: 74px; width: 1px; height: 118px; background: var(--rule); }
  .person { position: absolute; left: 283px; top: 72px; white-space: nowrap; }
  .person__name { color: var(--red); font-weight: 700; font-size: 15px; line-height: 18px; }
  .person__title { color: var(--ink); font-size: 12px; line-height: 18px; }
  .contacts { position: absolute; left: 281px; top: 124px; list-style: none; }
  .contacts li {
    display: flex; align-items: center; gap: 7px; height: 17.5px;
    color: var(--muted); font-size: 10.5px; letter-spacing: -0.15px; white-space: nowrap;
  }
  .contacts svg { width: 10px; height: 10px; fill: var(--charcoal); flex: none; }
  .address { position: absolute; left: 42px; top: 258px; color: var(--on-dark); font-size: 11.5px; line-height: 15px; white-space: nowrap; }
  .web { position: absolute; left: 108px; top: 261px; color: var(--on-dark); font-size: 13px; white-space: nowrap; }
</style>
</head>
<body>
<main class="stage">
  <section class="card card--front" aria-label="Business card front">
    <svg class="card__wave" viewBox="0 0 525 299" aria-hidden="true">
      <path d="M0 247 Q210 226 525 256 L525 266 Q210 238 0 257 Z" fill="var(--red)"/>
      <path d="M0 260 Q210 242 525 270 L525 299 L0 299 Z" fill="var(--charcoal)"/>
    </svg>
    <div class="brand"><span class="brand__mark"></span><span class="brand__name">Varentoria</span></div>
    <div class="divider"></div>
    <div class="person">
      <p class="person__name">Derek Hanford</p>
      <p class="person__title">Prime Capacity Officer</p>
    </div>
    <ul class="contacts">
      <li><svg viewBox="0 0 10 10"><path d="M2 0.5 L4 2.6 L3 3.8 Q4 6 6.2 7 L7.4 6 L9.5 8 L8 9.6 Q3 9 0.4 2 Z"/></svg>1300 582 714</li>
      <li><svg viewBox="0 0 10 10"><path d="M3 0 H7 V10 H3 Z M3.8 1 V7.5 H6.2 V1 Z" fill-rule="evenodd"/></svg>0412 637 258</li>
      <li><svg viewBox="0 0 10 10"><path d="M0 2 H10 V8.5 H0 Z M0.5 2.5 L5 5.8 L9.5 2.5 Z" fill-rule="evenodd"/></svg>derek.hanford@varentoria-example.com.au</li>
      <li><svg viewBox="0 0 10 10"><circle cx="5" cy="5" r="5"/></svg>www.varentoria-example.com.au</li>
    </ul>
    <p class="address">Level 29, Marlow Tower<br>7 Marlow Square Sydney, NSW 2000 Australia</p>
  </section>

  <section class="card card--back" aria-label="Business card back">
    <svg class="card__wave" viewBox="0 0 525 299" aria-hidden="true">
      <path d="M0 247 Q210 226 525 256 L525 266 Q210 238 0 257 Z" fill="var(--red)"/>
      <path d="M0 260 Q210 242 525 270 L525 299 L0 299 Z" fill="var(--charcoal)"/>
    </svg>
    <div class="brand"><span class="brand__mark"></span><span class="brand__name">Varentoria</span></div>
    <p class="web">www.varentoria-example.com.au</p>
  </section>
</main>
</body>
</html>
```